Business Card front and back

I am looking for business card design. I really really like the design file I uploaded named 627788_19250069_3478263_85f427ee_image

Target Market(s)

Corporate Fitness High end Private country club

Industry/Entity Type

Fitness Industry

Contact Information for Business Card

The last image I like as an example I uploaded a bunch of my logos. The file labeled "the signature" is my business card information for you to use

Colors
0054AA
0677BA
7BADD7
CADEEF
E8F1F8

Requirements
Must have
• E-mail sigThe file I uploaded labeled "627788_19250069_3478263_85f427ee_image" with all the plus signs on the back if those could be the logo symbol I uploaded labeled "1 back.png"

```html
<!DOCTYPE html>
<html lang="en">
<head>
<meta charset="utf-8">
<title>Peakform Studio – Business Cards</title>
<link rel="stylesheet" href="https://fonts.googleapis.com/css2?family=Poppins:wght@400;500;600&family=Saira:ital,wght@1,700&family=Open+Sans:wght@400;600&display=swap">
<style>
  :root {
    --stage: #151515;
    --card: #2c2c2c;
    --card-deep: #232323;
    --pattern-light: #4a4a4a;
    --pattern-dark: #121212;
    --brand-blue: #3d7cc9;
    --text-light: #f2f2f2;
    --text-soft: #d9d9d9;
    --mark-dark: #050505;
    --mark-sheen: #3a3a3a;
  }
  * { box-sizing: border-box; margin: 0; padding: 0; }
  html, body { width: 1200px; height: 1015px; overflow: hidden; background: var(--stage); }
  .canvas { position: relative; width: 1200px; height: 1015px; }

  .card {
    position: absolute; width: 740px; height: 423px;
    background: var(--card); overflow: hidden;
    box-shadow: 0 10px 30px rgba(0,0,0,.55);
  }
  .card--back  { left: 70px;  top: 50px; }
  .card--front { left: 390px; top: 540px; }

  /* back side */
  .pattern-field {
    position: absolute; inset: 0;
    background: linear-gradient(200deg, var(--pattern-light) 0%, var(--card) 45%, var(--pattern-dark) 100%);
  }
  .back-content {
    position: absolute; inset: 0;
    display: flex; flex-direction: column; align-items: center; justify-content: center;
    text-align: center; padding-top: 10px;
  }
  .brand-lockup { display: flex; align-items: center; gap: 12px; margin-bottom: 26px; }
  .brand-square { width: 26px; height: 26px; background: var(--brand-blue); }
  .brand-name {
    font-family: "Poppins", sans-serif; font-weight: 600; font-size: 30px;
    letter-spacing: 3px; text-transform: uppercase; color: var(--text-light);
  }
  .offerings-title {
    font-family: "Poppins", sans-serif; font-weight: 400; font-size: 26px;
    color: var(--brand-blue); margin-bottom: 10px;
  }
  .offerings-list { list-style: none; font-family: "Poppins", sans-serif; font-size: 20px; line-height: 1.3; color: var(--text-light); }

  /* front side */
  .mark-panel {
    position: absolute; right: 50px; top: 55px; width: 300px; height: 300px;
    border-radius: 0 90px 90px 0;
    background: linear-gradient(150deg, var(--mark-sheen) 0%, var(--mark-dark) 55%);
  }
  .contact {
    position: absolute; left: 70px; top: 150px;
    font-family: "Open Sans", sans-serif; color: var(--text-light);
  }
  .person-name {
    font-family: "Saira", sans-serif; font-style: italic; font-weight: 700; font-size: 34px;
    color: var(--brand-blue); text-transform: uppercase; letter-spacing: 1px; line-height: 1;
  }
  .person-role { font-size: 19px; color: var(--text-soft); margin: 4px 0 28px 8px; }
  .contact-list { list-style: none; margin-left: 24px; }
  .contact-list li { display: flex; align-items: center; gap: 12px; font-size: 19px; line-height: 1.45; }
  .contact-list svg { width: 20px; height: 20px; fill: var(--brand-blue); flex: none; }
</style>
</head>
<body>
<main class="canvas">

  <section class="card card--back" aria-label="Card back">
    <div class="pattern-field" role="img" aria-label="Repeating brand symbol pattern in embossed greys"></div>
    <div class="back-content">
      <div class="brand-lockup">
        <span class="brand-square"></span>
        <span class="brand-name">Peakform Studio</span>
      </div>
      <h2 class="offerings-title">Offerings</h2>
      <ul class="offerings-list">
        <li>Conceptual Planning - Equipment Specifications</li>
        <li>Equipment Procurement - 3rd Party Collaboration</li>
        <li>Preventative Maintenance Service</li>
      </ul>
    </div>
  </section>

  <section class="card card--front" aria-label="Card front">
    <div class="mark-panel" role="img" aria-label="Large glossy black brand symbol"></div>
    <div class="contact">
      <h1 class="person-name">Dana Morrow</h1>
      <p class="person-role">Principal</p>
      <ul class="contact-list">
        <li><svg viewBox="0 0 24 24"><path d="M12 2a7 7 0 0 0-7 7c0 5 7 13 7 13s7-8 7-13a7 7 0 0 0-7-7zm0 9.5A2.5 2.5 0 1 1 12 6.5a2.5 2.5 0 0 1 0 5z"/></svg>CO.WY.MT.ID.UT</li>
        <li><svg viewBox="0 0 24 24"><path d="M6.6 10.8a15 15 0 0 0 6.6 6.6l2.2-2.2a1 1 0 0 1 1-.25 11.4 11.4 0 0 0 3.6.57 1 1 0 0 1 1 1V20a1 1 0 0 1-1 1A17 17 0 0 1 3 4a1 1 0 0 1 1-1h3.5a1 1 0 0 1 1 1c0 1.250.2 2.450.57 3.570a1 1 0 0 1-.25 1z"/></svg>555-014-2290</li>
        <li><svg viewBox="0 0 24 24"><path d="M2 5h20v14H2zm2 2v.5l8 5 8-5V7z"/></svg>dana@peakformstudio.co</li>
        <li><svg viewBox="0 0 24 24"><path d="M12 2a10 10 0 1 0 0 20 10 10 0 0 0 0-20zm6.9 9h-3a15 15 0 0 0-1.3-5.6A8 8 0 0 1 18.9 11zM12 4.1c.9 1.2 1.7 3.6 1.9 6.9h-3.8c.2-3.3 1-5.700 1.9-6.9zM9.4 5.4A15 15 0 0 0 8.1 11h-3a8 8 0 0 1 4.3-5.6zM5.1 13h3a15 15 0 0 0 1.3 5.6A8 8 0 0 1 5.1 13zm6.9 6.9c-.9-1.2-1.7-3.6-1.9-6.9h3.8c-.2 3.3-1 5.7-1.9 6.9zm2.6-1.3a15 15 0 0 0 1.3-5.6h3a8 8 0 0 1-4.3 5.6z"/></svg>www.peakformstudio.co</li>
      </ul>
    </div>
  </section>

</main>
</body>
</html>
```